MS word document templates for consultancy

I need the following templates for my business using my logo as branding.

- General report template
- Letter head template
- Tender proposal template

The templates should be sleek and with minimal colors, but with a small amount of green and grey where appropriate (as per attached logo and email signature). Font should be consistent with the text in the email signature.

```html
<!DOCTYPE html>
<html lang="en">
<head>
<meta charset="UTF-8">
<title>Bellmont Advisory Letterhead</title>
<link href="https://fonts.googleapis.com/css2?family=Poppins:ital,wght@0,400;0,500;1,400&family=Space+Mono:wght@400;700&display=swap" rel="stylesheet">
<style>
  :root {
    --brand-green: #2e9a4b;
    --ink: #1d1d1b;
    --paper: #ffffff;
  }
  * { box-sizing: border-box; margin: 0; padding: 0; }
  html, body {
    width: 849px;
    height: 1200px;
    overflow: hidden;
    background: var(--paper);
  }
  .letterhead {
    position: relative;
    width: 849px;
    height: 1200px;
    background: var(--paper);
    border: 20px solid var(--brand-green);
  }
  .brand {
    position: absolute;
    top: 46px;
    left: 0;
    right: 0;
    text-align: center;
    font-family: "Poppins", sans-serif;
    font-weight: 400;
    font-size: 38px;
    line-height: 1.2;
    color: var(--ink);
  }
  .sender {
    position: absolute;
    left: 68px;
    top: 1067px;
  }
  .sender-name {
    font-family: "Space Mono", monospace;
    font-weight: 700;
    font-size: 19px;
    line-height: 1.3;
    letter-spacing: 0.5px;
    color: var(--brand-green);
  }
  .sender-role {
    margin-top: 8px;
    font-family: "Poppins", sans-serif;
    font-style: italic;
    font-size: 15px;
    line-height: 1.3;
    color: var(--brand-green);
  }
  .contact {
    position: absolute;
    left: 651px;
    top: 1073px;
  }
  .contact-label {
    font-family: "Space Mono", monospace;
    font-weight: 700;
    font-size: 11px;
    line-height: 1.3;
    letter-spacing: 4px;
    color: var(--brand-green);
  }
  .contact-value {
    margin-top: 12px;
    font-family: "Poppins", sans-serif;
    font-size: 15px;
    line-height: 1.3;
    color: var(--ink);
  }
</style>
</head>
<body>
  <main class="letterhead">
    <header class="brand">Bellmont Advisory</header>

    <footer>
      <div class="sender">
        <p class="sender-name">DANA WHITLOW</p>
        <p class="sender-role">Managing Director</p>
      </div>
      <div class="contact">
        <p class="contact-label">PHONE</p>
        <p class="contact-value">0400 555 019</p>
      </div>
    </footer>
  </main>
</body>
</html>
```